4th Generation Family Business Needs a New Card Design!

We are a family owned 4th Generation company. We are based in the Sydney, Australia area and we are desperately in need of a more modern and classy card. We are monumental masons who design, supply & erect lasting memorials throughout cemeteries in Sydney. Our customers are normally in a period of grieving. I have attached logo files that will need to be implemented on the card. Company was established 1935. Australian Owned and Operated. Card needs to be designed to PIXO.com specification.

Target Market(s)

Our target market is based upon people that a grieving for family members that have passed away. We also deal with alot of companies that own and operate cemeteries.

Industry/Entity Type

Business

Contact Information for Business Card

Simon Harcourt, Operations Manager, 0417293086, simon@harcourtmemorials.com.au
Lewis Harcourt, Director, 0491630572, lewis@harcourtmemorials.com.au
Phone # 02 9561 3048
Website: www.harcourtmemorials.com.au
Address: Suite 17, 8 Palfrey Lane, West Carlow, Sydney NSW 2156

Font styles to use
Serif
Decorative
Script

Requirements
Must have
• Would like to see the logo nicely implemented with a modern design. Embossed lettering would be a nice additive.

```html
<!DOCTYPE html>
<html lang="en">
<head>
<meta charset="utf-8">
<title>Harcourt Memorials – Business Card</title>
<link rel="stylesheet" href="https://fonts.googleapis.com/css2?family=Montserrat:wght@400;500;700&display=swap">
<style>
  :root {
    --bg: #3a3a3a;
    --card: #050505;
    --gold: #f2c21b;
    --white: #ffffff;
    --muted: #e6e6e6;
  }
  * { margin: 0; padding: 0; box-sizing: border-box; }
  html, body { width: 1200px; height: 900px; overflow: hidden; }
  body {
    background: var(--bg);
    font-family: "Montserrat", Arial, sans-serif;
    position: relative;
  }
  .card {
    position: absolute;
    width: 620px;
    height: 354px;
    background: var(--card);
    border-radius: 22px;
    color: var(--white);
    box-shadow: 0 14px 30px rgba(0,0,0,0.45);
  }
  .card--front { left: 140px; top: 70px; }
  .card--back { left: 440px; top: 476px; }

  .brand {
    display: flex;
    align-items: center;
    gap: 12px;
    font-weight: 700;
    color: var(--white);
    letter-spacing: 0.06em;
    text-transform: uppercase;
    line-height: 1.15;
  }
  .brand__square {
    width: 16px; height: 16px;
    background: var(--gold);
    flex: none;
  }
  .card--front .brand {
    position: absolute;
    left: 0; right: 0; top: 120px;
    justify-content: center;
    font-size: 30px;
  }
  .card--front .web {
    position: absolute;
    left: 0; right: 0; top: 262px;
    text-align: center;
    font-size: 14px;
    font-weight: 500;
  }
  .web__accent { color: var(--gold); font-weight: 700; }

  .card--back .brand {
    position: absolute;
    left: 40px; top: 150px;
    font-size: 22px;
    width: 250px;
  }
  .contact {
    position: absolute;
    left: 340px; top: 84px;
  }
  .contact__name {
    color: var(--gold);
    font-weight: 700;
    font-size: 22px;
  }
  .contact__role {
    font-size: 13px;
    margin: 2px 0 10px;
  }
  .contact__address {
    font-size: 12px;
    line-height: 1.45;
    margin-bottom: 6px;
    color: var(--muted);
  }
  .contact__list { list-style: none; }
  .contact__list li {
    display: flex;
    align-items: center;
    gap: 9px;
    font-size: 12px;
    line-height: 1.65;
    color: var(--muted);
  }
  .contact__list svg { width: 11px; height: 11px; flex: none; }
</style>
</head>
<body>
  <section class="card card--front">
    <div class="brand"><span class="brand__square"></span>Harcourt Memorials</div>
    <p class="web">www.<span class="web__accent">harcourtmemorials</span>.com.au</p>
  </section>

  <section class="card card--back">
    <div class="brand"><span class="brand__square"></span>Harcourt Memorials</div>
    <div class="contact">
      <p class="contact__name">Lewis Harcourt</p>
      <p class="contact__role">Director</p>
      <p class="contact__address">Suite 17, 8 Palfrey Lane<br>West Carlow, Sydney NSW 2156</p>
      <ul class="contact__list">
        <li>
          <svg viewBox="0 0 12 12"><rect x="3" y="0.5" width="6" height="11" rx="1.2" fill="none" stroke="#f2c21b" stroke-width="1.2"/></svg>
          0491630572
        </li>
        <li>
          <svg viewBox="0 0 12 12"><path d="M2.5 1 L4.5 1 L5.3 3.5 L4 4.5 Q5 7 7.5 8 L8.5 6.7 L11 7.5 L11 9.5 Q10.5 11 9 11 Q1 10 1 2.8 Q1 1 2.5 1Z" fill="#f2c21b"/></svg>
          02 9561 3048
        </li>
        <li>
          <svg viewBox="0 0 12 12"><rect x="0.6" y="2" width="10.8" height="8" fill="none" stroke="#f2c21b" stroke-width="1.2"/><path d="M0.6 2 L6 6.5 L11.4 2" fill="none" stroke="#f2c21b" stroke-width="1.2"/></svg>
          lewis@harcourtmemorials.com.au
        </li>
        <li>
          <svg viewBox="0 0 12 12"><circle cx="6" cy="6" r="5.2" fill="none" stroke="#f2c21b" stroke-width="1.2"/><path d="M0.8 6 H11.2 M6 0.8 Q3 6 6 11.2 M6 0.8 Q9 6 6 11.2" fill="none" stroke="#f2c21b" stroke-width="1"/></svg>
          www.<span class="web__accent">harcourtmemorials</span>.com.au
        </li>
      </ul>
    </div>
  </section>
</body>
</html>
```